Bright Wave Labs

We need a professional letter head format for our company. Now we have a logo but need to desing a new logo also. I have uploaded our old logo. Use the color in the logo and design a new one.

Dear Designers , Need to mention "BWL" and please dont use our old LOGO. we need a new catchy one.

```html
<!DOCTYPE html>
<html lang="en">
<head>
<meta charset="utf-8">
<title>Bright Wave Labs — Letterhead</title>
<link href="https://fonts.googleapis.com/css2?family=Open+Sans:wght@400;600&family=Lato:wght@400&display=swap" rel="stylesheet">
<style>
  :root {
    --navy: #132f4c;
    --green: #9bc53a;
    --ink: #4a4a4a;
    --ink-dark: #333333;
    --paper: #ffffff;
  }
  * { margin: 0; padding: 0; box-sizing: border-box; }
  html, body { width: 1040px; height: 1200px; overflow: hidden; background: var(--paper); }
  .letterhead {
    position: relative;
    width: 1040px; height: 1200px;
    background: var(--paper);
    font-family: "Open Sans", Arial, sans-serif;
    color: var(--ink);
  }

  /* plain header and footer bands */
  .header-band { position: absolute; top: 0; left: 0; width: 1040px; height: 58px; background: var(--navy); }
  .header-rule { position: absolute; top: 64px; left: 0; width: 1040px; height: 6px; background: var(--green); }
  .footer-rule { position: absolute; top: 1078px; left: 0; width: 1040px; height: 6px; background: var(--green); }
  .footer-band { position: absolute; top: 1090px; left: 0; width: 1040px; height: 110px; background: var(--navy); }

  .brand {
    position: absolute; right: 110px; top: 164px;
    display: flex; align-items: center; gap: 10px;
  }
  .brand-dot { width: 14px; height: 14px; border-radius: 50%; background: var(--green); }
  .brand-name { font-weight: 600; font-size: 26px; line-height: 34px; color: var(--navy); }

  .block { position: absolute; left: 98px; width: 840px; font-size: 15px; line-height: 19px; }
  .issue-date { top: 216px; }
  .recipient { top: 252px; }
  .salutation { top: 356px; }
  .para {
    font-size: 16.2px; line-height: 27px;
    text-align: justify; hyphens: auto;
  }
  .para-1 { top: 408px; }
  .para-2 { top: 569px; }
  .para-3 { top: 678px; }
  .closing { top: 814px; }
  .signatory-name { top: 890px; font-size: 19px; line-height: 26px; color: var(--ink-dark); }
  .signatory-title { top: 922px; }

  .footer-address {
    position: absolute; left: 101px; top: 1148px;
    font-family: "Lato", Arial, sans-serif; font-size: 18px; line-height: 24px; color: #fff;
  }
  .footer-contacts {
    position: absolute; right: 103px; top: 1108px;
    font-family: "Lato", Arial, sans-serif; font-size: 18px; line-height: 22px; color: #fff;
    text-align: right;
  }
  .contact-line { display: flex; justify-content: flex-end; align-items: center; gap: 6px; }
  .contact-line svg { width: 15px; height: 15px; fill: #fff; }
</style>
</head>
<body>
<main class="letterhead">
  <div class="header-band"></div>
  <div class="header-rule"></div>

  <div class="brand">
    <span class="brand-dot"></span>
    <span class="brand-name">Bright Wave Labs</span>
  </div>

  <p class="block issue-date">Issuing Date: May 5, 2018</p>
  <p class="block recipient">Name Of Employee Mr. XYZABC<br>Address of Employee<br>Address Line 2 etc..</p>
  <p class="block salutation">Dear Mr.XYZABC</p>
  <p class="block para para-1">Lorem Ipsum has been the industry's standard dummy text ever since the 1500s, when an unknown printer took a galley of type and scrambled it to make a type specimen book. It has survived not only five centuries, but also the leap into electronic typesetting, remaining essentially unchanged. It was popularised in the 1960s with the release of Ridgeline sheets containing Lorem Ipsum passages, and more recently with desktop publishing software like Quillset Press including versions of Lorem Ipsum.</p>
  <p class="block para para-2">Lorem Ipsum is simply dummy text of the printing and typesetting industry. Lorem Ipsum has been the industry's standard dummy text ever since the 1500s, when an unknown printer took a galley of type and scrambled it to make a type specimen book.</p>
  <p class="block para para-3">It has survived not only five centuries, but also the leap into electronic typesetting, remaining essentially unchanged. It was popularised in the 1960s with the release of Ridgeline sheets containing Lorem IpsumIpsum passages.</p>
  <p class="block closing">Yours Sincerely</p>
  <p class="block signatory-name">Daniel Reeves</p>
  <p class="block signatory-title">Managing Director</p>

  <div class="footer-rule"></div>
  <div class="footer-band"></div>

  <p class="footer-address">421, Address line here, 45452,Country Name</p>

  <div class="footer-contacts">
    <div class="contact-line">044-987 654 321
      <svg viewBox="0 0 16 16" aria-hidden="true"><path d="M3 2h3l1 3-2 1.5a8 8 0 0 0 4.5 4.5L11 9l3 1v3a1 1 0 0 1-1 1A11 11 0 0 1 2 3a1 1 0 0 1 1-1z"/></svg>
    </div>
    <div class="contact-line">hello@brightwavelabs.com
      <svg viewBox="0 0 16 16" aria-hidden="true"><rect x="1" y="3" width="14" height="10" rx="1"/><path d="M1.5 4 8 9l6.5-5" stroke="var(--navy)" stroke-width="1.4" fill="none"/></svg>
    </div>
    <div class="contact-line">www.brightwavelabs.com
      <svg viewBox="0 0 16 16" aria-hidden="true"><circle cx="8" cy="8" r="7"/><path d="M1 8h14M8 1c-3 4-3 10 0 14M8 1c3 4 3 10 0 14" stroke="var(--navy)" stroke-width="1.2" fill="none"/></svg>
    </div>
  </div>
</main>
</body>
</html>
```